Start up Events company needs a business card design

We are a brand new start up events company that need an impressively designed business card to make the best first impression with our future clients.

Description on company:
- start-up company
- in the events management industry
- selling flagship children related event
- our future clients will mostly be vendors in the alternative education industry. dance schools, music schools, sports camp facilitators, academic establishments
- our target market are kids, parents of kids, mass market

What we need in the business card:
- we currently have a rough design that I have uploaded. we need to brush it up. make it look more professional, more vibrant but keep the meaning of the company which is called "Lantern & Kite"
- a reason for the "Lantern & Kite" concept is because we will be starting off with a flagship event & be branching out into all other related businesses relating to our core highlight which is kids & alternative education.
- this is a tentative logo we have selected - which is a girl on a swing. to represent momentum as a start up company and related to children
- if you have a better logo alternative, please do suggest it to us
- we need more colours, vibrancy yet it has to be sleek and professional.

As we are a start-up company, our budget is tight. If you have a good idea / concept, do take on this project overlooking the tight budget.
If you require any additional information, do feel free to drop us messages!

Thank you designers!

```html
<!DOCTYPE html>
<html lang="en">
<head>
<meta charset="utf-8">
<title>Hub &amp; Spokes — Business Card</title>
<link rel="stylesheet" href="https://fonts.googleapis.com/css2?family=Oswald:wght@500;600&family=Roboto:wght@300;400&display=swap">
<style>
  :root {
    --page: #f2f2f0;
    --frame-grey: #e3e3e3;
    --panel-white: #ffffff;
    --panel-grey: #e8e8e8;
    --ink: #111111;
    --band: #14213d;
    --text: #2f2f2f;
    --accent: #ff5a36;
    --accent-2: #f7b32b;
    --shadow: rgba(0, 0, 0, 0.18);
  }
  * { box-sizing: border-box; margin: 0; padding: 0; }
  html, body { width: 1200px; height: 1019px; overflow: hidden; }
  body {
    background: var(--page);
    display: flex;
    flex-direction: column;
    align-items: center;
    justify-content: center;
    gap: 56px;
  }
  .card {
    width: 760px;
    height: 434px;
    position: relative;
    box-shadow: 0 10px 28px var(--shadow);
  }

  /* Front */
  .card--front { background: var(--frame-grey); }
  .card--front .panel {
    position: absolute;
    inset: 44px;
    background: var(--panel-white);
    border-left: 8px solid var(--accent);
  }
  .logo-art {
    position: absolute;
    left: 130px;
    top: 60px;
    width: 180px;
    height: 145px;
    background: linear-gradient(160deg, var(--accent), var(--accent-2));
    border-radius: 6px;
  }
  .identity {
    position: absolute;
    left: 300px;
    top: 215px;
    max-width: 340px;
  }
  .identity__name {
    font-family: "Oswald", sans-serif;
    font-weight: 600;
    font-size: 36px;
    letter-spacing: 1px;
    color: var(--band);
    text-transform: uppercase;
    line-height: 1;
    white-space: nowrap;
  }
  .identity__role {
    font-family: "Roboto", sans-serif;
    font-weight: 400;
    font-size: 21px;
    color: var(--accent);
    margin-top: 8px;
  }

  /* Back */
  .card--back { background: var(--band); }
  .card--back .panel {
    position: absolute;
    inset: 0 72px 70px 0;
    background: var(--panel-grey);
    border-bottom: 8px solid var(--accent);
  }
  .contacts {
    position: absolute;
    left: 210px;
    top: 70px;
    list-style: none;
    font-family: "Roboto", sans-serif;
    font-weight: 300;
    font-size: 21px;
    color: var(--text);
  }
  .contacts li {
    display: flex;
    align-items: flex-start;
    gap: 14px;
    margin-bottom: 12px;
    line-height: 1.3;
  }
  .contacts li.address { margin-bottom: 20px; }
  .contacts svg {
    width: 18px;
    height: 18px;
    flex: none;
    margin-top: 4px;
    fill: var(--accent);
  }
</style>
</head>
<body>
  <section class="card card--front">
    <div class="panel">
      <div class="logo-art" role="img" aria-label="Silhouette of a child on a swing"></div>
      <div class="identity">
        <p class="identity__name">Marcus Ellery</p>
        <p class="identity__role">Managing Director</p>
      </div>
    </div>
  </section>

  <section class="card card--back">
    <div class="panel">
      <ul class="contacts">
        <li class="address">
          <svg viewBox="0 0 24 24" aria-hidden="true"><path d="M12 2a7 7 0 0 0-7 7c0 5 7 13 7 13s7-8 7-13a7 7 0 0 0-7-7zm0 9.5A2.5 2.5 0 1 1 12 6.5a2.5 2.5 0 0 1 0 5z"/></svg>
          <span>27 Kiteway Lane,<br>Harbour Road HSP</span>
        </li>
        <li>
          <svg viewBox="0 0 24 24" aria-hidden="true"><path d="M6.6 10.8a15 15 0 0 0 6.6 6.6l2.2-2.2a1 1 0 0 1 1-.25 11.4 11.4 0 0 0 3.6.57 1 1 0 0 1 1 1V20a1 1 0 0 1-1 1A17 17 0 0 1 3 4a1 1 0 0 1 1-1h3.5a1 1 0 0 1 1 1c0 1.250.2 2.45.57 3.57a1 1 0 0 1-.25 1z"/></svg>
          <span>012 555 0147</span>
        </li>
        <li>
          <svg viewBox="0 0 24 24" aria-hidden="true"><path d="M7 1h10a2 2 0 0 1 2 2v18a2 2 0 0 1-2 2H7a2 2 0 0 1-2-2V3a2 2 0 0 1 2-2zm0 3v15h10V4z"/></svg>
          <span>012 555 0148</span>
        </li>
        <li>
          <svg viewBox="0 0 24 24" aria-hidden="true"><path d="M3 5h18a1 1 0 0 1 1 1v12a1 1 0 0 1-1 1H3a1 1 0 0 1-1-1V6a1 1 0 0 1 1-1zm1 2.3V17h16V7.3l-8 5.2z"/></svg>
          <span>hello@hubspokes.com</span>
        </li>
        <li>
          <svg viewBox="0 0 24 24" aria-hidden="true"><path d="M12 2a10 10 0 1 0 0 20 10 10 0 0 0 0-20zm6.9 9h-3a15 15 0 0 0-1.3-5.6A8 8 0 0 1 18.9 11zM12 4c.9 1.2 1.8 3.6 1.9 7h-3.8C10.2 7.6 11.1 5.2 12 4zM9.4 5.4A15 15 0 0 0 8.1 11h-3a8 8 0 0 1 4.3-5.6zM5.1 13h3a15 15 0 0 0 1.3 5.6A8 8 0 0 1 5.1 13zM12 20c-.9-1.2-1.8-3.6-1.9-7h3.8c-.1 3.4-1 5.8-1.9 7zm2.6-1.4a15 15 0 0 0 1.3-5.6h3a8 8 0 0 1-4.3 5.6z"/></svg>
          <span>www.hubspokes.com</span>
        </li>
      </ul>
    </div>
  </section>
</body>
</html>
```